Construction Company

Design a clutter free business card, it can be double-sided utilizing the logo for VKM Ltd simple with all relevant contact information.

Please also a letterhead design to function for the purposes of invoicing, all mail requirements, with header to be distinctive while the footer ties page together and incorporates all necessary information.

For now, please use generic / dummy text and when a winner is selected, I will disclose the contact information.

Hi Designers! Please read the updated brief which includes the design of a business card and letterhead. Thank you!

```html
<!DOCTYPE html>
<html lang="en">
<head>
<meta charset="utf-8">
<title>VKM Ltd — Business Card</title>
<link rel="stylesheet" href="https://fonts.googleapis.com/css2?family=Playfair+Display:wght@700&family=Roboto:wght@400;500&display=swap">
<style>
  :root {
    --navy: #1f3190;
    --navy-deep: #1a2a80;
    --royal: #28399c;
    --gold: #c19a2e;
    --paper: #ffffff;
    --stage: #dcdcda;
    --ink-grey: #555a66;
  }
  * { margin: 0; padding: 0; box-sizing: border-box; }
  html, body { width: 1200px; height: 801px; overflow: hidden; }
  body {
    background: var(--stage);
    display: flex; align-items: center; justify-content: center; gap: 40px;
    font-family: "Roboto", Arial, sans-serif;
  }
  .card {
    position: relative;
    width: 540px; height: 309px;
    border: 3px solid var(--gold);
    overflow: hidden;
    box-shadow: 0 10px 26px rgba(0,0,0,.22);
  }

  /* Front */
  .card-front { background: var(--paper); }
  .front-logo {
    position: absolute; left: 40px; top: 100px; width: 200px;
    display: flex; align-items: center; gap: 10px;
  }
  .logo-mark { width: 16px; height: 16px; border-radius: 50%; background: var(--navy); flex: none; }
  .logo-name {
    font-family: "Playfair Display", Georgia, serif; font-weight: 700;
    font-size: 40px; letter-spacing: 1px; color: var(--navy); line-height: 1;
  }
  .divider {
    position: absolute; left: 250px; top: 66px; width: 1.5px; height: 120px;
    background: var(--navy);
  }
  .identity { position: absolute; left: 278px; top: 62px; }
  .person-name {
    font-family: "Playfair Display", Georgia, serif; font-weight: 700;
    font-size: 22px; color: var(--navy); letter-spacing: .5px;
  }
  .person-title { font-weight: 500; font-size: 15px; color: var(--gold); margin-top: 2px; }
  .contacts { list-style: none; margin-top: 14px; }
  .contacts li {
    display: flex; align-items: center; gap: 9px;
    font-size: 15px; color: var(--ink-grey); line-height: 23px;
  }
  .contacts svg { width: 14px; height: 14px; fill: var(--navy); flex: none; }
  .address-band {
    position: absolute; left: 0; right: 0; bottom: 24px; height: 36px;
    background: var(--navy);
    display: flex; align-items: center; gap: 10px; padding-left: 22px;
    color: var(--paper); font-size: 15px; letter-spacing: .3px;
  }
  .address-band svg { width: 13px; height: 17px; fill: var(--paper); flex: none; }
  .band-accent {
    position: absolute; right: 0; bottom: 24px; width: 56px; height: 36px;
    background: var(--gold);
  }

  /* Back */
  .card-back { background: var(--royal); }
  .back-pattern {
    position: absolute; inset: 0;
    background: radial-gradient(ellipse at 55% 40%, #2c3ea4 0%, var(--royal) 55%, var(--navy-deep) 100%);
  }
  .back-logo {
    position: absolute; left: 0; right: 0; top: 130px;
    display: flex; justify-content: center; align-items: center; gap: 12px;
  }
  .back-logo .logo-mark { background: var(--paper); }
  .back-logo .logo-name { color: var(--paper); font-size: 46px; }
</style>
</head>
<body>

  <article class="card card-front">
    <div class="front-logo">
      <span class="logo-mark"></span>
      <span class="logo-name">VKM LTD</span>
    </div>
    <div class="divider"></div>
    <div class="identity">
      <h1 class="person-name">DANIEL REED</h1>
      <p class="person-title">Director</p>
      <ul class="contacts">
        <li><svg viewBox="0 0 24 24"><path d="M6.6 10.8a15.1 15.1 0 0 0 6.6 6.6l2.2-2.2a1 1 0 0 1 1-.25 11.4 11.4 0 0 0 3.6.57 1 1 0 0 1 1 1V20a1 1 0 0 1-1 1A17 17 0 0 1 3 4a1 1 0 0 1 1-1h3.5a1 1 0 0 1 1 1c0 1.25.2 2.45.57 3.57a1 1 0 0 1-.25 1z"/></svg>555.210.4400</li>
        <li><svg viewBox="0 0 24 24"><path d="M2 5h20v14H2zm2 2v.5l8 5 8-5V7zm0 3v7h16v-7l-8 5z"/></svg>info@vkmltd.com</li>
        <li><svg viewBox="0 0 24 24"><circle cx="12" cy="12" r="10"/></svg>www.vkmltd.com</li>
      </ul>
    </div>
    <div class="address-band">
      <svg viewBox="0 0 20 26"><path d="M10 0a9 9 0 0 0-9 9c0 7 9 17 9 17s9-10 9-17a9 9 0 0 0-9-9zm0 12.5A3.5 3.5 0 1 1 10 5.5a3.5 3.5 0 0 1 0 7z"/></svg>
      Harbour House, 12 Mill Lane, London, N4 2LX
    </div>
    <div class="band-accent"></div>
  </article>

  <article class="card card-back">
    <div class="back-pattern" role="img" aria-label="Embossed tone-on-tone floral pattern across the card"></div>
    <div class="back-logo">
      <span class="logo-mark"></span>
      <span class="logo-name">VKM LTD</span>
    </div>
  </article>

</body>
</html>
```